Vantor Ridge needs a Business Card Design

We need a business card design for an Information Technology company based in Fairfax Virginia called Vantor Ridge. We want the business card to use our logo colors. We need it to be double-sided. The business card needs to look professional but we would like it to be unique. You can get company information from our web site (http://www.vantorridgellc.example).

Target Market(s)

Target market is Government Agencies and Business Professionals.

Industry/Entity Type

Business

Requirements
Must have
• Must have section for company name, company address, company URL, employee name, title, phone and email. Also must have company logo and space for entering logos.

```html
<!DOCTYPE html>
<html lang="en">
<head>
<meta charset="utf-8">
<title>Vantor Ridge – Business Card</title>
<link rel="stylesheet" href="https://fonts.googleapis.com/css2?family=Open+Sans:wght@400;600;700&display=swap">
<style>
  :root {
    --bg: #e9eaec;
    --paper: #ffffff;
    --brand-blue: #0a78c2;
    --brand-blue-deep: #0a5ea6;
    --brand-navy: #283a93;
    --ink: #4a4a4a;
    --white: #ffffff;
  }
  * { margin: 0; padding: 0; box-sizing: border-box; }
  html, body {
    width: 1200px; height: 1024px; overflow: hidden;
    background: var(--bg);
    font-family: "Open Sans", Arial, sans-serif;
  }
  .canvas { position: relative; width: 1200px; height: 1024px; }
  .card {
    position: absolute;
    box-shadow: 0 6px 18px rgba(0,0,0,.18);
    overflow: hidden;
  }

  /* Front: portrait */
  .card-front {
    left: 102px; top: 214px; width: 340px; height: 595px;
    background: var(--paper);
  }
  .identity {
    position: absolute; right: 30px; top: 34px; text-align: right;
  }
  .person-name {
    color: var(--brand-blue); font-weight: 700; font-size: 15px; letter-spacing: .3px;
  }
  .person-title {
    color: var(--brand-navy); font-weight: 700; font-size: 10px; letter-spacing: .6px; margin-top: 2px;
  }
  .contact {
    position: absolute; right: 30px; top: 112px;
    list-style: none; text-align: right; color: var(--ink); font-size: 10.5px; line-height: 15px;
  }
  .contact li { display: flex; justify-content: flex-end; align-items: flex-start; gap: 8px; }
  .contact .lines { display: block; }
  .contact .group { margin-bottom: 10px; }
  .contact svg { width: 10px; height: 10px; margin-top: 2px; flex: none; fill: var(--brand-blue); }
  .front-band {
    position: absolute; left: 0; right: 0; top: 290px; bottom: 90px;
    background: var(--brand-blue);
  }
  .front-band-base {
    position: absolute; left: 0; right: 0; bottom: 0; height: 90px;
    background: var(--brand-navy);
  }

  /* Back: landscape */
  .card-back {
    left: 502px; top: 342px; width: 595px; height: 340px;
    background: linear-gradient(135deg, var(--brand-blue) 0%, var(--brand-blue-deep) 100%);
    color: var(--white);
  }
  .wordmark {
    position: absolute; left: 150px; top: 118px;
    display: flex; align-items: center; gap: 14px;
  }
  .wordmark-square { width: 40px; height: 40px; background: var(--brand-navy); }
  .wordmark-name {
    font-weight: 700; font-size: 38px; letter-spacing: 1px; text-transform: uppercase; line-height: 1;
    color: var(--white);
  }
  .tagline {
    position: absolute; left: 204px; top: 168px;
    font-size: 10.5px; letter-spacing: .8px; text-transform: uppercase;
  }
  .back-url {
    position: absolute; left: 36px; bottom: 30px; font-size: 12px; letter-spacing: .3px;
  }
</style>
</head>
<body>
<main class="canvas">

  <section class="card card-front" aria-label="Business card front">
    <header class="identity">
      <p class="person-name">DANIEL MERCER</p>
      <p class="person-title">JOB TITLE</p>
    </header>

    <ul class="contact">
      <li class="group">
        <span class="lines">1480 Harlow Ave, Suite 310<br>Linden Falls, OH 43215</span>
        <svg viewBox="0 0 10 10" aria-hidden="true"><path d="M5 0.5 9.5 4.5H8V9.5H6V6.5H4V9.5H2V4.5H0.5Z"/></svg>
      </li>
      <li>
        <span>877.555.0142</span>
        <svg viewBox="0 0 10 10" aria-hidden="true"><path d="M2 0.5 4 2.8 3 4a6 6 0 0 0 3 3l1.2-1 2.3 2-1.3 1.5C4.5 9.5 0.5 5.5 0.5 1.8Z"/></svg>
      </li>
      <li class="group">
        <span>888.555.0197</span>
        <svg viewBox="0 0 10 10" aria-hidden="true"><rect x="1" y="3" width="8" height="5"/><rect x="3" y="1" width="4" height="2"/></svg>
      </li>
      <li>
        <span>name@vantorridgellc.example</span>
        <svg viewBox="0 0 10 10" aria-hidden="true"><path d="M0.5 2H9.5V8H0.5Z M1 2.5 5 5.5 9 2.5" fill="none" stroke="#0a78c2" stroke-width="1"/></svg>
      </li>
      <li>
        <span>www.vantorridgellc.example</span>
        <svg viewBox="0 0 10 10" aria-hidden="true"><circle cx="5" cy="5" r="4.3" fill="none" stroke="#0a78c2" stroke-width="1"/><path d="M0.7 5H9.3M5 0.7C3 3 3 7 5 9.3M5 0.7C7 3 7 7 5 9.3" fill="none" stroke="#0a78c2" stroke-width=".8"/></svg>
      </li>
    </ul>

    <div class="front-band"></div>
    <div class="front-band-base"></div>
  </section>

  <section class="card card-back" aria-label="Business card back">
    <div class="wordmark">
      <span class="wordmark-square" aria-hidden="true"></span>
      <span class="wordmark-name">Vantor Ridge</span>
    </div>
    <p class="tagline">Turning bold ideas into lasting results</p>
    <p class="back-url">www.vantorridgellc.example</p>
  </section>

</main>
</body>
</html>
```